The most modern business card ever !!!

Our company call “Vendalo”. Vendalo is a technology company specialized in cruises solutions. Out main product is a platform to reserve cruises. This is a revolutionary platform that make easier to travel agencies and final users to reserve cruises across dozen companies like tibba, wernu, hpv, dgb, etc..We are a “start up”, with a young team of developers and we want to transmit it.. For it, we want something different, a modern business card that represent cruises and technology.. When someone receive this card, this person should say: wowww this is different… this is modern… this is a cruise related company..
- diferent, modern
- traditions business card

```html
<!DOCTYPE html>
<html lang="en">
<head>
<meta charset="UTF-8">
<title>Vendalo – Business Card</title>
<link rel="stylesheet" href="https://fonts.googleapis.com/css2?family=Open+Sans:wght@400;700&family=Exo+2:wght@600&display=swap">
<style>
  :root {
    --backdrop: #2c2c2e;
    --card: #0f0f10;
    --card-edge: #1a1a1c;
    --accent: #29a9e1;
    --ink-light: #f2f2f2;
    --ink-muted: #9a9a9c;
    --rule: #4a4a4c;
  }
  * { margin: 0; padding: 0; box-sizing: border-box; }
  html, body {
    width: 1200px; height: 900px; overflow: hidden;
    background: var(--backdrop);
    font-family: "Open Sans", Arial, sans-serif;
  }
  .stage {
    width: 1200px; height: 900px;
    display: flex; flex-direction: column; align-items: center; justify-content: center;
    gap: 44px;
  }
  .card {
    position: relative;
    width: 560px; height: 320px;
    background: linear-gradient(160deg, var(--card-edge), var(--card) 60%);
    box-shadow: 0 14px 30px rgba(0,0,0,.45);
    overflow: hidden;
  }
  .card__band {
    position: absolute; left: 0; right: 0; bottom: 0;
    height: 9px; background: var(--accent);
  }
  .card--front { display: flex; align-items: center; justify-content: center; }
  .brand-name {
    font-family: "Exo 2", "Open Sans", sans-serif;
    font-weight: 600; font-size: 66px; letter-spacing: 1px;
    color: var(--ink-light);
    margin-bottom: 14px;
  }
  .card--back { padding: 0 40px; }
  .card__details {
    position: absolute; top: 92px; left: 0; right: 0;
    display: flex; justify-content: center;
  }
  .identity {
    text-align: right; padding-right: 20px; padding-top: 4px;
    border-right: 1px solid var(--rule); height: 82px;
  }
  .identity__name {
    font-weight: 700; font-size: 19px; color: var(--accent); letter-spacing: .5px;
  }
  .identity__role { font-size: 15px; color: var(--ink-muted); margin-top: -2px; }
  .contact { list-style: none; padding-left: 18px; padding-top: 4px; }
  .contact__item {
    display: flex; align-items: center; gap: 9px;
    font-size: 16px; line-height: 21px; color: var(--ink-muted);
  }
  .contact__icon { width: 12px; height: 12px; fill: var(--accent); flex: none; }
  .address {
    position: absolute; left: 0; right: 0; top: 230px;
    text-align: center; font-size: 16px; color: var(--ink-muted); letter-spacing: .2px;
  }
</style>
</head>
<body>
<main class="stage">
  <section class="card card--front" aria-label="Card front">
    <h1 class="brand-name">Vendalo</h1>
    <div class="card__band"></div>
  </section>

  <section class="card card--back" aria-label="Card back">
    <div class="card__details">
      <div class="identity">
        <p class="identity__name">MARA QUELL</p>
        <p class="identity__role">Managing Director</p>
      </div>
      <ul class="contact">
        <li class="contact__item">
          <svg class="contact__icon" viewBox="0 0 12 12"><path d="M1 3.5C1 2 2.5 1 6 1s5 1 5 2.5V5H8.5V3.8h-5V5H1z"/><rect x="2" y="6" width="8" height="5" rx="1"/></svg>
          044-555 018 274
        </li>
        <li class="contact__item">
          <svg class="contact__icon" viewBox="0 0 12 12"><path d="M3.5 0h5a1 1 0 0 1 1 1v10a1 1 0 0 1-1 1h-5a1 1 0 0 1-1-1V1a1 1 0 0 1 1-1zm.5 1.5v8h4v-8z"/></svg>
          044-555 018 274
        </li>
        <li class="contact__item">
          <svg class="contact__icon" viewBox="0 0 12 12"><path d="M0 2h12v8H0zm1.2 1L6 6.5 10.8 3z"/></svg>
          hello@vendalo.com
        </li>
        <li class="contact__item">
          <svg class="contact__icon" viewBox="0 0 12 12"><circle cx="6" cy="6" r="6"/></svg>
          www.vendalo.com
        </li>
      </ul>
    </div>
    <p class="address">12345, Address Goes Here Country Name, 123456.</p>
    <div class="card__band"></div>
  </section>
</main>
</body>
</html>
```